A flyer for future customers to get acquainted with our company

The flyer/card is intended for intermediaries. The purpose of this flyer is to introduce businesses to Valdro.

It should convey: real estate and financing, with actual images. Various keywords describing what we do: project financing, temporary real estate financing, real estate financing, investment properties, transformations. We distinguish ourselves by being fast, flexible, and personal.

Please ensure the front has an attractive and inviting appearance, and leave space on the back for additional text.

Color codes: #E85B35 en #091E33

```html
<!DOCTYPE html>
<html lang="nl">
<head>
<meta charset="utf-8">
<title>Valdro – kaart voor tussenpersonen</title>
<link href="https://fonts.googleapis.com/css2?family=Montserrat:wght@300;400;500;600;700&family=Poppins:wght@600;700;800&family=Oswald:wght@500;600&display=swap" rel="stylesheet">
<style>
:root{
  --orange:#E85B35;
  --navy:#091E33;
  --navy-mid:#132f55;
  --blue-btn:#1f4e9a;
  --white:#ffffff;
  --stage:#e9eaec;
  --stamp:#e4e4e4;
  --line:#3a3a3a;
}
*{box-sizing:border-box;margin:0;padding:0}
html,body{width:1200px;height:2400px;overflow:hidden;background:var(--stage);font-family:'Montserrat',sans-serif}
.card{position:absolute;left:100px;width:1000px;height:667px;background:var(--white);overflow:hidden;box-shadow:0 10px 28px rgba(0,0,0,.25)}
.card--front{top:140px}
.card--back{top:1250px}
.abs{position:absolute}

/* brand */
.brand{position:absolute;display:flex;align-items:center;gap:10px;font-family:'Montserrat',sans-serif;font-weight:700;color:var(--navy);letter-spacing:-1px}
.brand__dot{width:18px;height:18px;border-radius:50%;background:var(--orange)}

/* front */
.front-band{left:0;top:393px;width:1000px;height:274px;background:var(--navy)}
.front-visual{left:0;top:0}
.headline{left:35px;top:140px;color:var(--navy)}
.headline__kicker{font-size:22px;font-weight:400;letter-spacing:.5px}
.headline__main{font-family:'Poppins',sans-serif;font-weight:700;color:var(--orange);font-size:60px;line-height:62px;margin-top:2px}
.headline__cond{font-family:'Oswald',sans-serif;font-weight:600;font-size:42px;line-height:44px;letter-spacing:-.5px;transform:scaleX(.92);transform-origin:left}
.headline__sub{font-family:'Poppins',sans-serif;font-weight:700;font-size:33px;line-height:36px}
.headline__since{font-size:16px;font-weight:500;margin-top:4px}

.feature{width:160px;text-align:center;top:357px;color:var(--white)}
.feature__icon{display:block;margin:0 auto}
.feature__label{font-size:24px;font-weight:300;margin-top:14px}
.sep{width:0;border-left:1px dashed #7d8da3;top:405px;height:82px}
.dash{border-top:1px dashed #8a97aa;height:0}

.services-title{font-family:'Poppins',sans-serif;font-weight:700;font-size:26px;color:var(--white)}
.services-title span{color:var(--orange)}
.ticks{list-style:none;color:var(--white)}
.ticks li{display:flex;align-items:flex-start;gap:9px;margin-bottom:9px}
.tick{flex:none;width:15px;height:15px;margin-top:2px}
.ticks--front li{font-size:16.5px;font-weight:500;margin-bottom:11px}

.contact{color:var(--white);font-family:'Poppins',sans-serif;font-weight:600;font-size:20px;display:flex;align-items:center;gap:8px}
.visit{left:570px;top:600px;width:392px;height:32px;display:flex;font-family:'Poppins',sans-serif}
.visit__label{width:118px;background:var(--blue-btn);color:var(--white);font-size:14px;font-weight:600;letter-spacing:1.5px;display:flex;align-items:center;justify-content:center}
.visit__url{flex:1;background:var(--orange);color:var(--white);font-size:22px;font-weight:700;letter-spacing:3.5px;display:flex;align-items:center;justify-content:center}

/* back */
.back-orange{left:0;top:0;width:517px;height:373px;background:var(--orange)}
.back-navy{left:0;top:373px;width:517px;height:294px;background:var(--navy)}
.intro{left:35px;top:35px;width:450px;font-size:12.5px;line-height:15px;font-weight:700;color:var(--navy)}
.svc{width:225px;display:flex;gap:10px;color:var(--white)}
.svc__icon{flex:none}
.svc__title{font-family:'Poppins',sans-serif;font-size:12.5px;font-weight:700;color:#fff}
.svc__text{font-size:11px;line-height:12.6px;margin-top:2px}
.back-title{left:35px;top:388px;font-family:'Poppins',sans-serif;font-weight:700;font-size:20px;color:var(--white)}
.back-title span{color:var(--orange)}
.ticks--back li{font-size:12.5px;line-height:14px;width:215px}
.back-phone{left:35px;top:552px;font-family:'Poppins',sans-serif;font-weight:600;font-size:28px;color:var(--white);display:flex;align-items:center;gap:10px}
.back-url{left:35px;top:596px;font-family:'Poppins',sans-serif;font-weight:700;font-size:26px;letter-spacing:5px;color:var(--white)}
.back-url span{color:var(--orange)}
.stamp{left:815px;top:35px;width:150px;height:172px;background:var(--stamp)}
.address-line{left:600px;width:363px;border-top:1.5px solid var(--line)}
</style>
</head>
<body>

<!-- FRONT -->
<section class="card card--front" aria-label="Voorzijde">
  <div class="abs front-band"></div>

  <svg class="abs front-visual" width="1000" height="667" viewBox="0 0 1000 667">
    <defs>
      <radialGradient id="deskTone" cx="50%" cy="45%" r="60%">
        <stop offset="0" stop-color="#f4f4f4"/>
        <stop offset=".7" stop-color="#d9dadc"/>
        <stop offset="1" stop-color="#8b6e62"/>
      </radialGradient>
    </defs>
    <circle cx="748" cy="278" r="258" fill="var(--navy)"/>
    <circle cx="772" cy="266" r="247" fill="var(--orange)"/>
    <circle cx="772" cy="270" r="205" fill="var(--white)"/>
    <circle cx="772" cy="270" r="196" fill="url(#deskTone)" role="img" aria-label="Foto: overhandigen van geld boven een contract met huismodel en rekenmachine"/>
  </svg>

  <div class="brand" style="left:35px;top:40px;font-size:74px;">valdro<span class="brand__dot"></span></div>

  <div class="abs headline">
    <div class="headline__kicker">VLOTTE ACCEPTATIE</div>
    <div class="headline__main">CREATIEVE</div>
    <div class="headline__cond">FINANCIERINGSOPLOSSINGEN</div>
    <div class="headline__sub">EN MAATWERK</div>
    <div class="headline__since">DAT IS WAT WE AL SINDS 2013 DOEN..</div>
  </div>

  <div class="abs feature" style="left:0px;">
    <svg class="feature__icon" width="76" height="76" viewBox="0 0 76 76">
      <circle cx="38" cy="38" r="35" fill="#fff" stroke="var(--orange)" stroke-width="5"/>
      <circle cx="38" cy="41" r="16" fill="none" stroke="var(--navy)" stroke-width="2.5"/>
      <rect x="34" y="20" width="8" height="4" fill="var(--navy)"/>
      <path d="M38 41 L44 34" stroke="var(--orange)" stroke-width="2.5" stroke-linecap="round"/>
    </svg>
    <div class="feature__label">Snel</div>
  </div>
  <div class="abs sep" style="left:152px;"></div>
  <div class="abs feature" style="left:153px;">
    <svg class="feature__icon" width="76" height="76" viewBox="0 0 76 76">
      <circle cx="38" cy="38" r="35" fill="#fff" stroke="var(--orange)" stroke-width="5"/>
      <circle cx="38" cy="38" r="12" fill="none" stroke="var(--navy)" stroke-width="2.5" stroke-dasharray="5 3"/>
      <circle cx="38" cy="38" r="5" fill="var(--orange)"/>
      <path d="M20 30 A20 20 0 0 1 52 24 M56 46 A20 20 0 0 1 24 52" fill="none" stroke="var(--orange)" stroke-width="2.5"/>
    </svg>
    <div class="feature__label">Flexibel</div>
  </div>
  <div class="abs sep" style="left:310px;"></div>
  <div class="abs feature" style="left:320px;">
    <svg class="feature__icon" width="76" height="76" viewBox="0 0 76 76">
      <circle cx="38" cy="38" r="35" fill="#fff" stroke="var(--orange)" stroke-width="5"/>
      <rect x="24" y="20" width="24" height="34" rx="2" fill="none" stroke="var(--navy)" stroke-width="2.5"/>
      <path d="M29 32h14M29 38h14M29 44h9" stroke="var(--navy)" stroke-width="2"/>
      <path d="M44 50 L54 30" stroke="var(--orange)" stroke-width="3" stroke-linecap="round"/>
    </svg>
    <div class="feature__label">Persoonlijk</div>
  </div>

  <div class="abs dash" style="left:33px;top:512px;width:482px;"></div>

  <div class="abs services-title" style="left:35px;top:533px;"><span>Wat</span> Wij Doen..</div>
  <ul class="abs ticks ticks--front" style="left:35px;top:582px;">
    <li><svg class="tick" viewBox="0 0 16 16"><circle cx="8" cy="8" r="8" fill="var(--orange)"/><path d="M4.5 8.2l2.3 2.3 4.6-4.8" fill="none" stroke="#fff" stroke-width="1.8"/></svg>Projectfinancieringen</li>
    <li><svg class="tick" viewBox="0 0 16 16"><circle cx="8" cy="8" r="8" fill="var(--orange)"/><path d="M4.5 8.2l2.3 2.3 4.6-4.8" fill="none" stroke="#fff" stroke-width="1.8"/></svg>Tijdelijke vastgoedfinancieringen</li>
  </ul>
  <ul class="abs ticks ticks--front" style="left:340px;top:554px;">
    <li><svg class="tick" viewBox="0 0 16 16"><circle cx="8" cy="8" r="8" fill="var(--orange)"/><path d="M4.5 8.2l2.3 2.3 4.6-4.8" fill="none" stroke="#fff" stroke-width="1.8"/></svg>vastgoedfinancieringen</li>
    <li><svg class="tick" viewBox="0 0 16 16"><circle cx="8" cy="8" r="8" fill="var(--orange)"/><path d="M4.5 8.2l2.3 2.3 4.6-4.8" fill="none" stroke="#fff" stroke-width="1.8"/></svg>Vastgoedbeleggingen</li>
    <li><svg class="tick" viewBox="0 0 16 16"><circle cx="8" cy="8" r="8" fill="var(--orange)"/><path d="M4.5 8.2l2.3 2.3 4.6-4.8" fill="none" stroke="#fff" stroke-width="1.8"/></svg>Transformaties</li>
  </ul>

  <div class="abs contact" style="left:572px;top:560px;">
    <svg width="16" height="16" viewBox="0 0 16 16"><circle cx="8" cy="8" r="8" fill="var(--orange)"/><path d="M5 4.5l1.6 0 .7 2-1 .8a6 6 0 0 0 2.4 2.4l.8-1 2 .7v1.6c-3.8.4-6.9-2.7-6.5-6.5z" fill="#fff"/></svg>
    (088) 555 01 23
  </div>
  <div class="abs contact" style="left:798px;top:558px;font-size:19px;">
    <svg width="15" height="15" viewBox="0 0 16 16"><circle cx="8" cy="8" r="8" fill="var(--orange)"/><rect x="4" y="5" width="8" height="6" fill="#fff"/><path d="M4 5l4 3.5L12 5" fill="none" stroke="var(--orange)" stroke-width="1"/></svg>
    info@valdro.nl
  </div>
  <div class="abs visit">
    <div class="visit__label">Visit Us At</div>
    <div class="visit__url">www.valdro.nl</div>
  </div>
</section>

<!-- BACK -->
<section class="card card--back" aria-label="Achterzijde">
  <div class="abs back-orange"></div>
  <div class="abs back-navy"></div>

  <p class="abs intro">Iedere aanvraag bekijken we vanuit jouw ogen. We geven een eerlijk oordeel over je casus en geven binnen enkele dagen commitment, zodat jij je kunt focussen op je plannen.</p>

  <div class="abs svc" style="left:35px;top:100px;">
    <svg class="svc__icon" width="36" height="36" viewBox="0 0 36 36"><circle cx="18" cy="18" r="16" fill="#fff" stroke="var(--navy)" stroke-width="2"/><path d="M10 19h16M12 15h12M12 23h12" stroke="var(--orange)" stroke-width="2"/></svg>
    <div><div class="svc__title">Handelsfinanciering</div><div class="svc__text">Voor de vastgoedondernemer die onroerend goed aankoopt, renoveert en doorverkoopt.</div></div>
  </div>
  <div class="abs svc" style="left:272px;top:100px;">
    <svg class="svc__icon" width="36" height="36" viewBox="0 0 36 36"><circle cx="18" cy="18" r="16" fill="#fff" stroke="var(--navy)" stroke-width="2"/><path d="M11 18a7 7 0 0 1 12-5M25 18a7 7 0 0 1-12 5" fill="none" stroke="var(--orange)" stroke-width="2"/></svg>
    <div><div class="svc__title">Transformatiefinanciering</div><div class="svc__text">Wil je vastgoed aankopen en met een bestemmingswijziging waarde toevoegen?</div></div>
  </div>
  <div class="abs svc" style="left:35px;top:180px;">
    <svg class="svc__icon" width="36" height="36" viewBox="0 0 36 36"><circle cx="18" cy="18" r="16" fill="#fff" stroke="var(--navy)" stroke-width="2"/><path d="M10 21h16M12 21a6 6 0 0 1 12 0" fill="none" stroke="var(--orange)" stroke-width="2"/></svg>
    <div><div class="svc__title">Bouwfinanciering</div><div class="svc__text">Een pand kopen maar tijdelijk geen liquiditeit beschikbaar voor de aankoop of afbouw?</div></div>
  </div>
  <div class="abs svc" style="left:272px;top:180px;">
    <svg class="svc__icon" width="36" height="36" viewBox="0 0 36 36"><circle cx="18" cy="18" r="16" fill="#fff" stroke="var(--navy)" stroke-width="2"/><path d="M14 27V10h9M14 13l8 3" fill="none" stroke="var(--orange)" stroke-width="2"/></svg>
    <div><div class="svc__title">Nieuwbouwfinanciering</div><div class="svc__text">Van scratch af aan een beleggingspand of ander commercieel vastgoed realiseren?</div></div>
  </div>
  <div class="abs svc" style="left:35px;top:260px;">
    <svg class="svc__icon" width="36" height="36" viewBox="0 0 36 36"><circle cx="18" cy="18" r="16" fill="#fff" stroke="var(--navy)" stroke-width="2"/><path d="M11 19l7-7 7 7M13 18v8h10v-8" fill="none" stroke="var(--orange)" stroke-width="2"/></svg>
    <div><div class="svc__title">Beleggingsfinanciering</div><div class="svc__text">De tijdelijke vastgoedfinan-ciering om te investeren in verhuurd en/of onverhuurd (commercieel) vastgoed.</div></div>
  </div>
  <div class="abs svc" style="left:272px;top:262px;">
    <svg class="svc__icon" width="36" height="36" viewBox="0 0 36 36"><circle cx="18" cy="18" r="16" fill="#fff" stroke="var(--navy)" stroke-width="2"/><circle cx="18" cy="20" r="6" fill="none" stroke="var(--orange)" stroke-width="2"/><path d="M15 12h6" stroke="var(--orange)" stroke-width="2"/></svg>
    <div><div class="svc__title">Stressfinanciering</div><div class="svc__text">Voor ondernemers die na een faillissement een doorstart willen maken en/of een lopende bancaire schuld willen inlossen.</div></div>
  </div>

  <div class="abs back-title">Vastgoedfinanciering <span>voor ondernemers</span></div>
  <ul class="abs ticks ticks--back" style="left:35px;top:432px;">
    <li><svg class="tick" viewBox="0 0 16 16" style="width:11px;height:11px"><circle cx="8" cy="8" r="8" fill="var(--orange)"/><path d="M4.5 8.2l2.3 2.3 4.6-4.8" fill="none" stroke="#fff" stroke-width="1.8"/></svg>Voor het handelen in onroerend goed</li>
    <li style="margin-top:14px"><svg class="tick" viewBox="0 0 16 16" style="width:11px;height:11px"><circle cx="8" cy="8" r="8" fill="var(--orange)"/><path d="M4.5 8.2l2.3 2.3 4.6-4.8" fill="none" stroke="#fff" stroke-width="1.8"/></svg>Voor transformatie van kantoorgebouwen naar appartementen</li>
  </ul>
  <ul class="abs ticks ticks--back" style="left:228px;top:432px;width:280px;">
    <li style="width:280px"><svg class="tick" viewBox="0 0 16 16" style="width:11px;height:11px"><circle cx="8" cy="8" r="8" fill="var(--orange)"/><path d="M4.5 8.2l2.3 2.3 4.6-4.8" fill="none" stroke="#fff" stroke-width="1.8"/></svg>Het realiseren van een nieuwbouwcomplex of woningen</li>
    <li style="width:280px;margin-top:14px"><svg class="tick" viewBox="0 0 16 16" style="width:11px;height:11px"><circle cx="8" cy="8" r="8" fill="var(--orange)"/><path d="M4.5 8.2l2.3 2.3 4.6-4.8" fill="none" stroke="#fff" stroke-width="1.8"/></svg>Het verbouwen van je beleggingspand of commercieel vastgoed</li>
  </ul>

  <div class="abs dash" style="left:35px;top:538px;width:265px;"></div>

  <svg class="abs" style="left:0;top:0" width="1000" height="667" viewBox="0 0 1000 667">
    <defs>
      <linearGradient id="deskWork" x1="0" y1="0" x2="1" y2="1">
        <stop offset="0" stop-color="#5a7290"/>
        <stop offset=".6" stop-color="#9aa6b4"/>
        <stop offset="1" stop-color="#2b3e58"/>
      </linearGradient>
    </defs>
    <circle cx="437" cy="668" r="154" fill="var(--orange)"/>
    <circle cx="455" cy="690" r="118" fill="url(#deskWork)" role="img" aria-label="Foto: hand die op een rekenmachine werkt aan een bureau"/>
  </svg>

  <div class="abs back-phone">
    <svg width="22" height="22" viewBox="0 0 16 16"><circle cx="8" cy="8" r="8" fill="var(--orange)"/><path d="M5 4.5l1.6 0 .7 2-1 .8a6 6 0 0 0 2.4 2.4l.8-1 2 .7v1.6c-3.8.4-6.9-2.7-6.5-6.5z" fill="#fff"/></svg>
    (088) 555 01 23
  </div>
  <div class="abs back-url">www.<span>valdro</span>.nl</div>

  <div class="brand" style="left:540px;top:45px;font-size:64px;">valdro<span class="brand__dot"></span></div>
  <div class="abs stamp"></div>
  <div class="abs address-line" style="top:300px;"></div>
  <div class="abs address-line" style="top:367px;"></div>
  <div class="abs address-line" style="top:435px;"></div>
</section>

</body>
</html>
```